ORLA - Óptica Médica - web design and concept

Website concept - Create and develop our website design and structure. ORLA is an optical store chain, and we are looking to establish our web and digital concept. In attachment there are several pictures about our stores and our logo.

The website structure should be user friendly. Colors should be light and the design as simple and minimalist as possible. There are different variations of the logothat can be used, check the file.

The website will include optical collections and sun collections as an online store. Also, a medical menu should be considered in order for clients to schedule optometry appointments. There should also be a menu for client assistance where the clients can read about glass maintenance in our workshop.
Updates

Low design quality

Number of Pages Required

5+ page

Font styles to use
Serif
Sans Serif

Requirements
Must have
• Must be user-friendly and minimalist.
• Please USE PICTURES FROM THE BRANDS we sell: MERUN, BOSKA, PNW, KOLE, BAMPE
Nice to have
• Nice to inspire: ZEK glasses (see website https://ch.shopzek.com/en/)
• Nice to inspire: https://merun-eyewear.com/
• Nice to ispire: https://www.pnwglobe.com/en/
Should not have
• Hysteric colors and shapes

```html
<!DOCTYPE html>
<html lang="en">
<head>
<meta charset="utf-8">
<title>ORLA Óptica Médica — Online Store</title>
<link href="https://fonts.googleapis.com/css2?family=Heebo:wght@300;400;500&family=Lato:wght@400;700&family=Cinzel:wght@400&display=swap" rel="stylesheet">
<style>
  :root{
    --ink:#1a1a1a;
    --text:#444;
    --muted:#777;
    --line:#d8d8dc;
    --accent:#e9a23b;
    --band:#f4f4f6;
    --footer:#000;
    --white:#fff;
  }
  *{box-sizing:border-box;margin:0;padding:0}
  html,body{width:1200px;height:2715px;overflow:hidden;background:var(--white)}
  body{position:relative;font-family:"Heebo",Arial,sans-serif;color:var(--text)}
  .abs{position:absolute}

  /* header */
  .social{display:flex;gap:9px}
  .social span{width:10px;height:10px;border-radius:50%;background:var(--ink);display:block}
  .header-social{left:160px;top:17px}
  .brand{left:0;width:1200px;top:14px;text-align:center}
  .brand-mark{width:30px;height:30px;border-radius:50%;border:2px solid var(--ink);margin:0 auto 6px}
  .brand-name{font-family:"Cinzel",serif;font-size:21px;letter-spacing:3px;color:var(--ink);line-height:1}
  .brand-sub{font-size:6px;letter-spacing:3px;color:var(--ink);margin-top:3px}
  .cart{left:818px;top:15px;font-size:11px;color:var(--ink);display:flex;align-items:center;gap:8px}
  .phone{left:935px;top:15px;font-size:11px;color:var(--ink);display:flex;align-items:center;gap:7px}
  .nav{left:313px;top:104px;display:flex;align-items:center;gap:22px;font-size:11px;color:var(--ink)}
  .nav .current{color:var(--accent)}
  .nav .cta{background:#000;color:var(--white);padding:4px 8px}

  .page-title{left:0;width:1200px;top:256px;text-align:center;font-weight:300;font-size:44px;color:var(--ink)}

  /* toolbar */
  .view-toggle{left:160px;top:475px;display:flex;gap:22px}
  .label{font-size:10px;color:var(--ink)}
  .select{position:absolute;top:475px;height:20px;border:1.5px solid var(--ink);font-size:10px;color:var(--ink);padding:2px 8px}
  .select::after{content:"";position:absolute;right:0;top:0;width:20px;height:100%;background:#000}
  .select::before{content:"";position:absolute;right:5px;top:6px;border:5px solid transparent;border-top:6px solid var(--white);z-index:1}

  /* products */
  .product{position:absolute;width:280px;text-align:center}
  .product-photo{width:172px;height:80px;margin:0 auto;border-radius:40px 40px 46px 46px}
  .product-name{font-weight:300;font-size:18px;color:var(--text);margin-top:14px}
  .product-price{font-size:18px;color:var(--text);margin-top:6px}
  .tone-dark{background:linear-gradient(#3a4452,#6a7584)}
  .tone-violet{background:linear-gradient(#3b2a6e,#8a6ac2)}
  .tone-rose{background:linear-gradient(#6b2f47,#d9a3b4)}
  .tone-amber{background:linear-gradient(#7a3e17,#5c5a50)}
  .tone-blue{background:linear-gradient(#3d4e6b,#a7b5c8)}
  .tone-smoke{background:linear-gradient(#222,#9a96a0)}
  .tone-brown{background:linear-gradient(#5a2a14,#b77a45)}
  .tone-taupe{background:linear-gradient(#4a3328,#b39a8a)}

  .pager{left:824px;top:1736px;display:flex;gap:7px;font-size:18px;font-weight:300;color:var(--ink);align-items:center}
  .pager .on{color:var(--accent)}

  /* services */
  .service{position:absolute;top:1886px;height:89px;border:2px solid var(--line);display:flex;align-items:center;justify-content:center;gap:14px}
  .service-title{font-weight:300;font-size:17px;color:var(--text);line-height:1}
  .service-sub{font-size:10px;color:var(--text)}

  /* brands */
  .brand-band{left:0;top:2013px;width:1200px;height:163px;background:var(--band)}
  .brand-logo{position:absolute;top:2075px;width:170px;margin-left:-85px;text-align:center;font-size:26px;font-weight:500;color:var(--ink);letter-spacing:1px}

  /* newsletter */
  .news-title{left:0;width:1200px;top:2211px;text-align:center;font-weight:300;font-size:26px;color:var(--text)}
  .news-rule{left:535px;top:2253px;width:130px;height:2px;background:var(--accent)}
  .news-form{left:302px;top:2288px;width:596px;height:70px;border:2px solid #c9c9d4;border-right:none}
  .news-input{position:absolute;left:30px;top:26px;font-size:10px;color:var(--ink)}
  .news-send{position:absolute;left:505px;top:-2px;width:91px;height:72px;border:2px solid var(--ink);display:flex;align-items:center;justify-content:center;background:var(--white)}

  /* footer */
  .footer{left:0;top:2395px;width:1200px;height:320px;background:var(--footer);font-family:"Lato",Arial,sans-serif;color:var(--white)}
  .f-brand{left:163px;top:50px}
  .f-mark{width:20px;height:20px;border-radius:50%;border:1.5px solid var(--accent);margin:0 0 4px 6px}
  .f-name{font-family:"Cinzel",serif;color:var(--accent);font-size:15px;letter-spacing:2px}
  .f-about{left:160px;top:112px;width:165px;font-size:10px;line-height:13px}
  .f-more{left:160px;top:160px;font-size:10px}
  .f-social{left:160px;top:180px}
  .f-social span{background:var(--white)}
  .f-col h4{font-size:13px;font-weight:700;margin-bottom:12px}
  .f-col ul{list-style:none;font-size:10px;line-height:16.3px}
  .f-col li::before{content:"•";margin-right:9px}
  .f-contact{font-size:10px;line-height:16px}
  .f-contact div{display:flex;gap:8px;align-items:flex-start}
  .f-rule{left:160px;top:222px;width:880px;height:1px;background:#777}
  .f-copy{left:160px;top:238px;font-size:11px}
  .f-legal{left:819px;top:238px;font-size:11px}
</style>
</head>
<body>

<header>
  <div class="abs social header-social" aria-label="Social links"><span></span><span></span><span></span><span></span><span></span></div>
  <div class="abs brand">
    <div class="brand-mark"></div>
    <div class="brand-name">ORLA</div>
    <div class="brand-sub">OPTICA MEDICA</div>
  </div>
  <div class="abs cart">
    <svg width="9" height="11" viewBox="0 0 9 11"><rect x="0" y="4" width="9" height="7" fill="#1a1a1a"/><path d="M2 4V2.5a2.5 2.5 0 0 1 5 0V4" fill="none" stroke="#1a1a1a" stroke-width="1.3"/></svg>
    Your Cart ( 0 )
  </div>
  <div class="abs phone">
    <svg width="10" height="10" viewBox="0 0 24 24"><path d="M6.6 10.8a15 15 0 0 0 6.6 6.6l2.2-2.2c.3-.3.7-.4 1-.2 1.1.4 2.3.6 3.6.6.6 0 1 .4 1 1V20c0 .6-.4 1-1 1A17 17 0 0 1 3 4c0-.6.4-1 1-1h3.5c.6 0 1 .4 1 1 0 1.3.2 2.5.6 3.6.1.3 0 .7-.2 1z" fill="#1a1a1a"/></svg>
    +012-555-204-7
  </div>
  <nav class="abs nav">
    <span>Home</span>
    <span class="current">Online store</span>
    <span>Company history</span>
    <span>Medical section</span>
    <span>Store</span>
    <span>Contact Us</span>
    <span class="cta">Make an Appoinment</span>
  </nav>
</header>

<h1 class="abs page-title">Online Store</h1>

<div class="abs view-toggle">
  <svg width="22" height="20" viewBox="0 0 22 20"><g fill="#1a1a1a"><rect x="0" y="0" width="6" height="5.5"/><rect x="8" y="0" width="6" height="5.5"/><rect x="16" y="0" width="6" height="5.5"/><rect x="0" y="7.2" width="6" height="5.5"/><rect x="8" y="7.2" width="6" height="5.5"/><rect x="16" y="7.2" width="6" height="5.5"/><rect x="0" y="14.5" width="6" height="5.5"/><rect x="8" y="14.5" width="6" height="5.5"/><rect x="16" y="14.5" width="6" height="5.5"/></g></svg>
  <svg width="22" height="20" viewBox="0 0 22 20"><g fill="#1a1a1a"><rect x="0" y="0" width="6" height="5.5"/><rect x="8" y="0" width="14" height="5.5"/><rect x="0" y="7.2" width="6" height="5.5"/><rect x="8" y="7.2" width="14" height="5.5"/><rect x="0" y="14.5" width="6" height="5.5"/><rect x="8" y="14.5" width="14" height="5.5"/></g></svg>
</div>
<span class="abs label" style="left:371px;top:480px">Collection</span>
<div class="select" style="left:434px;width:68px">Full</div>
<span class="abs label" style="left:637px;top:480px">Show</span>
<div class="select" style="left:672px;width:68px">12</div>
<span class="abs label" style="left:889px;top:480px">Show</span>
<div class="select" style="left:932px;width:110px">Recommended</div>

<main>
  <div class="product" style="left:131px;top:603px"><div class="product-photo tone-dark" role="img" aria-label="Black round sunglasses with grey lenses"></div><div class="product-name">Product Name</div><div class="product-price">€ 20</div></div>
  <div class="product" style="left:457px;top:603px"><div class="product-photo tone-violet" role="img" aria-label="Cat-eye sunglasses with violet gradient lenses"></div><div class="product-name">Product Name</div><div class="product-price">€ 18</div></div>
  <div class="product" style="left:787px;top:603px"><div class="product-photo tone-rose" role="img" aria-label="Oversized sunglasses with rose gradient lenses"></div><div class="product-name">Product Name</div><div class="product-price">€ 25</div></div>

  <div class="product" style="left:131px;top:900px"><div class="product-photo tone-amber" role="img" aria-label="Wooden frame sunglasses with dark lenses"></div><div class="product-name">Product Name</div><div class="product-price">€ 25</div></div>
  <div class="product" style="left:457px;top:900px"><div class="product-photo tone-blue" role="img" aria-label="Metal aviator sunglasses with blue lenses"></div><div class="product-name">Product Name</div><div class="product-price">€ 20</div></div>
  <div class="product" style="left:787px;top:900px"><div class="product-photo tone-smoke" role="img" aria-label="Black cat-eye sunglasses with smoke lenses"></div><div class="product-name">Product Name</div><div class="product-price">€ 25</div></div>

  <div class="product" style="left:131px;top:1198px"><div class="product-photo tone-brown" role="img" aria-label="Tortoiseshell sunglasses with brown lenses"></div><div class="product-name">Product Name</div><div class="product-price">€ 15</div></div>
  <div class="product" style="left:457px;top:1198px"><div class="product-photo tone-smoke" role="img" aria-label="Square metal sunglasses with grey gradient lenses"></div><div class="product-name">Product Name</div><div class="product-price">€ 20</div></div>
  <div class="product" style="left:787px;top:1198px"><div class="product-photo tone-taupe" role="img" aria-label="Brown cat-eye sunglasses with taupe lenses"></div><div class="product-name">Product Name</div><div class="product-price">€ 20</div></div>

  <div class="product" style="left:131px;top:1503px"><div class="product-photo tone-dark" role="img" aria-label="Black round sunglasses with grey lenses"></div><div class="product-name">Product Name</div><div class="product-price">€ 25</div></div>
  <div class="product" style="left:457px;top:1503px"><div class="product-photo tone-blue" role="img" aria-label="Navy shield sunglasses with blue lenses"></div><div class="product-name">Product Name</div><div class="product-price">€ 10</div></div>
  <div class="product" style="left:787px;top:1503px"><div class="product-photo tone-violet" role="img" aria-label="Cat-eye sunglasses with violet gradient lenses"></div><div class="product-name">Product Name</div><div class="product-price">€ 20</div></div>

  <div class="abs pager">
    <svg width="10" height="12" viewBox="0 0 10 12"><path d="M7 1 2 6l5 5" fill="none" stroke="#1a1a1a" stroke-width="2"/></svg>
    <span class="on">1</span><span>2</span><span>3</span><span>4</span><span>5</span><span>6</span><span>7</span><span>8</span><span>9</span>
    <svg width="10" height="12" viewBox="0 0 10 12"><path d="M3 1l5 5-5 5" fill="none" stroke="#e9a23b" stroke-width="2"/></svg>
  </div>
</main>

<section>
  <div class="service" style="left:165px;width:286px">
    <svg width="26" height="30" viewBox="0 0 26 30"><circle cx="13" cy="12" r="10" fill="none" stroke="#222" stroke-width="2"/><path d="M9 26h8M13 22v4" stroke="#222" stroke-width="2"/></svg>
    <div><div class="service-title">Free Shipping</div><div class="service-sub">Lorem Ipsum is dummy text.</div></div>
  </div>
  <div class="service" style="left:460px;width:284px">
    <svg width="28" height="30" viewBox="0 0 28 30"><circle cx="14" cy="13" r="11" fill="none" stroke="#222" stroke-width="2"/><path d="M10 12a4 4 0 0 1 8 0v4h-8z" fill="none" stroke="#222" stroke-width="1.6"/><path d="M8 26h12" stroke="#222" stroke-width="2"/></svg>
    <div><div class="service-title">Premium Support</div><div class="service-sub">24/7 Customer service</div></div>
  </div>
  <div class="service" style="left:753px;width:284px">
    <svg width="40" height="28" viewBox="0 0 40 28"><path d="M2 4h22v16H2zM24 9h8l6 6v5H24z" fill="none" stroke="#222" stroke-width="2"/><circle cx="9" cy="22" r="3.5" fill="#fff" stroke="#222" stroke-width="2"/><circle cx="31" cy="22" r="3.5" fill="#fff" stroke="#222" stroke-width="2"/></svg>
    <div><div class="service-title">Payment Method</div><div class="service-sub">Cash On Delivery</div></div>
  </div>
</section>

<section>
  <div class="abs brand-band"></div>
  <svg class="abs" style="left:78px;top:2072px" width="22" height="42" viewBox="0 0 22 42"><path d="M20 2 3 21l17 19" fill="none" stroke="#1a1a1a" stroke-width="2.5"/></svg>
  <svg class="abs" style="left:1100px;top:2072px" width="22" height="42" viewBox="0 0 22 42"><path d="M2 2l17 19L2 40" fill="none" stroke="#e9a23b" stroke-width="2.5"/></svg>
  <div class="brand-logo" style="left:232px">Solvane</div>
  <div class="brand-logo" style="left:420px">Cardel</div>
  <div class="brand-logo" style="left:601px">Mirelle</div>
  <div class="brand-logo" style="left:782px">Aubrin</div>
  <div class="brand-logo" style="left:963px">Tenko</div>
</section>

<section>
  <h2 class="abs news-title">Subscribe For Our Newsletter</h2>
  <div class="abs news-rule"></div>
  <div class="abs news-form">
    <span class="news-input">E-Mail Address</span>
    <div class="news-send">
      <svg width="38" height="28" viewBox="0 0 38 28"><path d="M2 2l34 12L2 26l6-12z M8 14h28" fill="none" stroke="#1a1a1a" stroke-width="2" stroke-linejoin="round"/></svg>
    </div>
  </div>
</section>

<footer class="abs footer">
  <div class="abs f-brand"><div class="f-mark"></div><div class="f-name">ORLA</div></div>
  <p class="abs f-about">Lorem Ipsum is simply dummy text of the printing and typesetting industry.</p>
  <span class="abs f-more">READ MORE.....</span>
  <div class="abs social f-social"><span></span><span></span><span></span><span></span><span></span></div>

  <div class="abs f-col" style="left:422px;top:85px">
    <h4>QUICK LINK</h4>
    <ul><li>Women</li><li>Men</li><li>Youth</li><li>Collections</li><li>Contact Us</li></ul>
  </div>
  <div class="abs f-col" style="left:635px;top:85px">
    <h4>ACCOUNT</h4>
    <ul><li>My Account</li><li>My Wishlist</li><li>Checkout</li><li>Create Account</li><li>Register</li></ul>
  </div>
  <div class="abs f-col" style="left:858px;top:85px">
    <h4>QUICK CONTACT</h4>
    <div class="f-contact">
      <div><svg width="10" height="12" viewBox="0 0 24 24"><path d="M6.6 10.8a15 15 0 0 0 6.6 6.6l2.2-2.2c.3-.3.7-.4 1-.2 1.1.4 2.3.6 3.6.6.6 0 1 .4 1 1V20c0 .6-.4 1-1 1A17 17 0 0 1 3 4c0-.6.4-1 1-1h3.5c.6 0 1 .4 1 1 0 1.3.2 2.5.6 3.6.1.3 0 .7-.2 1z" fill="#e9a23b"/></svg>+012-555-381-6</div>
      <div style="margin-top:9px"><svg width="10" height="12" viewBox="0 0 10 12"><rect x="0" y="3" width="10" height="7" fill="#e9a23b"/></svg>info@orlaopticamedica.com</div>
      <div style="margin-top:9px"><svg width="10" height="12" viewBox="0 0 10 12"><path d="M5 0a4 4 0 0 1 4 4c0 3-4 8-4 8S1 7 1 4a4 4 0 0 1 4-4z" fill="#e9a23b"/></svg><span>14 Linden Row,<br>Harwick Falls, NJ 08120</span></div>
    </div>
  </div>

  <div class="abs f-rule"></div>
  <span class="abs f-copy">CopyRight ©2018 Orla Optica Medica. All Right Reserve</span>
  <span class="abs f-legal">Privacy Policy - Terms &amp; Conditions</span>
</footer>

</body>
</html>
```